Flyer-Design für FUNKENHAUS
Zielgruppe
FUNKENHAUS kümmert sich dauerhaft um die Strom- und Gasverträge seiner privaten und gewerblichen Kunden. Konkret heißt das: Wir recherchieren jedes Jahr für den Kunden den günstigsten seriösen Strom/Gaslieferanten und wechseln den Kunden zu diesem Lieferanten. Wir übernehmen dabei sämliche Kommunikation mit Kunden, Lieferanten, Netzbetreibern etc. Der Kunde hat dauerhaft uns als Ansprechparter. Die Dienstleistung ist vergleichbar zu einem Steuerberater: Der Kunde bezahlt uns, damit wir uns um seine Verträge kümmern und für ihn sparen. Die Bezahlung erfolgt auf Provisionsbasis. 30% der durch einen Lieferantenwechsel eingesparten Kosten erhalten wir als Lohn. Das heißt für den Kunden: FUNKENHAUS hat dasselbe Ziel: Möglichst viel sparen, da dann auch das Kuchenstück (die 30%) für FUNKENHAUS größer ist. Außerdem hat der Kunde kein Risiko, denn wenn FUNKENHAUS nichts für ihn sparen kann, zahlt er auch nichts.
Die Zielgruppe des anzufertigenden Flyers sind Eigenheimbesitzer mit einer Gasheizung, d.h. eher ältere Menschen
Aufgabenstellung
Der Flyer (DIN A4) soll eine integrierte Antwortpostkarte enthalten, die ausgefüllt und ausgeschnitten an uns zurückgeschickt werden kann. Über die Postkarte kann dann bei uns ein Angebot angefordert werden.
Auf der Postkarte müssen damit für Strom und/oder Gas verschiedene Felder zur Verfügung stehen (Absendeadresse des Interessenten, Jahresverbrauch, derzeitige Preise, Kontaktmöglichkeiten & Sonderwünsche, etc.).
Da der Flyer über Briefmobil verteilt werden soll, wird auf den Flyer die Kundenadresse aufgedruckt ('An die Bewohner des Hauses....'. Dazu muss ein Feld freigehalten werden. Konkret muss das Layout entsprechend den Vorgaben der Post erstellt werden. Diese sind in einer angehängten .pdf zu finden auf Seite 37 der pdf (bzw. 35 des Dokuments)
Wegen Nachfrage: Der Flyer soll nicht gefaltet werden, er wird tatsächlich als nicht-umhüllte DIN-A4 Karte von der Post verteilt. Dazu muss die Empfängeradresse der Antwortpostkarte (d.h. Adresse von Funkenhaus) auf der Rückseite des Flyer angebracht werden.
Der Flyer soll unserem Corporate Design entsprechen, einiges an Material wird bereit gestellt
Das beigefügte Material muss nicht übernommen werden. Im Gegenteil wünschen wir gerne auch andere Vorschläge!

```html
<!DOCTYPE html>
<html lang="de">
<head>
<meta charset="utf-8">
<title>FUNKENHAUS – Flyer</title>
<link rel="stylesheet" href="https://fonts.googleapis.com/css2?family=Montserrat:wght@300;400;500;600;700&display=swap">
<style>
  :root {
    --orange: #ee7d05;
    --blue: #02559a;
    --grey: #e8e8e8;
    --white: #ffffff;
    --ink: #1a1a1a;
  }
  * { margin: 0; padding: 0; box-sizing: border-box; }
  html, body { width: 849px; height: 1200px; overflow: hidden; background: var(--white); }
  body { font-family: "Montserrat", Arial, sans-serif; position: relative; }

  .address-field {
    position: absolute; left: 0; top: 105px; width: 400px; height: 234px;
    background: var(--grey);
  }
  .address-field__line {
    position: absolute; left: 71px; top: 86px;
    font-size: 12px; font-weight: 400; color: var(--ink); letter-spacing: 0.2px;
  }

  .brand {
    position: absolute; left: 470px; top: 155px;
    display: flex; align-items: center; gap: 10px;
  }
  .brand__dot { width: 24px; height: 24px; border-radius: 50%; background: var(--orange); }
  .brand__name {
    font-size: 40px; font-weight: 500; color: var(--blue); letter-spacing: 0.3px; line-height: 1;
  }

  .hero {
    position: absolute; left: 0; top: 400px; width: 849px; height: 400px;
    background: var(--orange);
  }
  .hero__title {
    position: absolute; left: 35px; top: 48px;
    font-size: 47px; font-weight: 300; line-height: 46px; color: var(--white);
    letter-spacing: 0.8px; white-space: nowrap;
  }
  .hero__lead {
    position: absolute; left: 35px; top: 230px;
    font-size: 16px; font-weight: 400; line-height: 21.5px; color: var(--white);
    letter-spacing: 0.6px; white-space: nowrap;
  }
  .hero-figure { position: absolute; left: 505px; top: 264px; width: 344px; height: 536px; }

  .cut-line {
    position: absolute; left: 0; top: 799px; width: 849px; height: 0;
    border-top: 1.5px dashed var(--white); z-index: 2;
  }

  .steps {
    position: absolute; left: 0; top: 800px; width: 849px; height: 400px;
    background: var(--blue); color: var(--white);
  }
  .steps__title {
    position: absolute; left: 29px; top: 50px;
    font-size: 35px; font-weight: 300; letter-spacing: 1px; line-height: 1; white-space: nowrap;
  }
  .steps__arrows { position: absolute; left: 0; top: 0; width: 849px; height: 400px; }

  .step__badge { position: absolute; width: 90px; height: 90px; }
  .step__num { position: absolute; font-size: 40px; font-weight: 300; line-height: 1; }
  .step__text { position: absolute; width: 240px; text-align: center; }
  .step__head { font-size: 16px; font-weight: 600; line-height: 17px; letter-spacing: 0.4px; }
  .step__body { font-size: 9.3px; font-weight: 400; line-height: 11.5px; margin-top: 5px; white-space: nowrap; }
  .step__body b { font-weight: 700; }

  .cycle-label {
    position: absolute; left: 520px; top: 175px; width: 120px; text-align: center;
    font-size: 16px; font-weight: 600; line-height: 17px; letter-spacing: 0.4px;
  }
</style>
</head>
<body>

  <section class="address-field">
    <p class="address-field__line">AN DIE BEWOHNER DES HAUSES</p>
  </section>

  <div class="brand">
    <span class="brand__dot"></span>
    <span class="brand__name">FUNKENHAUS</span>
  </div>

  <section class="hero">
    <h1 class="hero__title">ÜBERFORDERT IM<br>DSCHUNGEL DER<br>STROMANBIETER?</h1>
    <p class="hero__lead">SIE MÖCHTEN EINEN PARTNER, DER IHNEN ALLE<br>ARBEIT ABNIMMT, UM FÜR SIE DEN GÜNSTIGSTEN<br>STROMANBIETER ZU FINDEN?</p>
  </section>

  <svg class="hero-figure" viewBox="0 0 344 536" role="img" aria-label="Illustration: Figur hält ein großes Schild mit rotem Fragezeichen">
    <defs>
      <linearGradient id="figureTone" x1="0" y1="0" x2="0" y2="1">
        <stop offset="0" stop-color="#02559a"/>
        <stop offset="0.45" stop-color="#ffffff"/>
        <stop offset="1" stop-color="#02559a"/>
      </linearGradient>
    </defs>
    <rect x="0" y="0" width="344" height="536" rx="60" fill="url(#figureTone)"/>
  </svg>

  <div class="cut-line"></div>

  <section class="steps">
    <h2 class="steps__title">SO EINFACH GEHT‘S:</h2>

    <svg class="steps__arrows" viewBox="0 0 849 400" aria-hidden="true">
      <defs>
        <linearGradient id="fadeRight" gradientUnits="userSpaceOnUse" x1="200" y1="238" x2="318" y2="238">
          <stop offset="0" stop-color="#fff" stop-opacity="0"/>
          <stop offset="0.4" stop-color="#fff"/>
        </linearGradient>
        <linearGradient id="fadeLeft" gradientUnits="userSpaceOnUse" x1="620" y1="238" x2="476" y2="238">
          <stop offset="0" stop-color="#fff" stop-opacity="0"/>
          <stop offset="0.4" stop-color="#fff"/>
        </linearGradient>
        <linearGradient id="fadeUp" gradientUnits="userSpaceOnUse" x1="455" y1="188" x2="516" y2="128">
          <stop offset="0" stop-color="#fff" stop-opacity="0"/>
          <stop offset="0.5" stop-color="#fff"/>
        </linearGradient>
        <linearGradient id="fadeDown" gradientUnits="userSpaceOnUse" x1="623" y1="122" x2="679" y2="189">
          <stop offset="0" stop-color="#fff" stop-opacity="0"/>
          <stop offset="0.5" stop-color="#fff"/>
        </linearGradient>
      </defs>
      <g fill="none" stroke-width="4" stroke-linecap="square">
        <line x1="200" y1="238" x2="316" y2="238" stroke="url(#fadeRight)"/>
        <polyline points="307,229 318,238 307,247" stroke="#fff"/>
        <line x1="620" y1="238" x2="478" y2="238" stroke="url(#fadeLeft)"/>
        <polyline points="487,229 476,238 487,247" stroke="#fff"/>
        <line x1="455" y1="188" x2="514" y2="130" stroke="url(#fadeUp)"/>
        <polyline points="501,130 516,128 515,143" stroke="#fff"/>
        <line x1="623" y1="122" x2="678" y2="188" stroke="url(#fadeDown)"/>
        <polyline points="679,173 680,190 664,189" stroke="#fff"/>
      </g>
    </svg>

    <!-- Schritt 1 -->
    <span class="step__num" style="left:60px; top:220px;">1</span>
    <svg class="step__badge" style="left:83px; top:193px;" viewBox="0 0 90 90" role="img" aria-label="Symbol: Finger tippt">
      <circle cx="45" cy="45" r="45" fill="var(--orange)"/>
      <circle cx="40" cy="27" r="11" fill="none" stroke="#fff" stroke-width="4"/>
      <path d="M36 27 a4 4 0 0 1 8 0 v18 h6 a4 4 0 0 1 4 0 h4 a4 4 0 0 1 5 4 v16 a8 8 0 0 1 -8 8 h-16 a8 8 0 0 1 -6 -3 l-9 -12 a4 4 0 0 1 6 -5 l6 5 z" fill="#fff"/>
    </svg>
    <div class="step__text" style="left:8px; top:292px;">
      <p class="step__head">TARIF-CHECK<br>ANFORDERN</p>
      <p class="step__body">Fordern Sie <b>kostenlos und unverbindlich</b><br>ein angebot für die senkung ihrer strom-<br>und /oder Gaskosten</p>
    </div>

    <!-- Schritt 2 -->
    <span class="step__num" style="left:335px; top:220px;">2</span>
    <svg class="step__badge" style="left:364px; top:193px;" viewBox="0 0 90 90" role="img" aria-label="Symbol: Waage">
      <circle cx="45" cy="45" r="45" fill="var(--orange)"/>
      <g fill="#fff">
        <circle cx="45" cy="18" r="4"/>
        <rect x="43" y="20" width="4" height="44"/>
        <rect x="20" y="25" width="50" height="3.5"/>
        <rect x="33" y="64" width="24" height="6" rx="2"/>
        <path d="M12 50 h20 a10 6 0 0 1 -20 0 z"/>
        <path d="M58 50 h20 a10 6 0 0 1 -20 0 z"/>
      </g>
      <g fill="none" stroke="#fff" stroke-width="2">
        <polyline points="13,50 22,28 31,50"/>
        <polyline points="59,50 68,28 77,50"/>
      </g>
    </svg>
    <div class="step__text" style="left:289px; top:292px;">
      <p class="step__head">BEST-TARIF<br>CHECK</p>
      <p class="step__body">Fordern Sie kostenlos und unverbindlich ein<br>angebot für die senkung ihrer strom- und /<br>oder Gaskosten</p>
    </div>

    <!-- Schritt 3 -->
    <span class="step__num" style="left:492px; top:71px;">3</span>
    <svg class="step__badge" style="left:520px; top:45px;" viewBox="0 0 90 90" role="img" aria-label="Symbol: Sparschwein mit Münze">
      <circle cx="45" cy="45" r="45" fill="var(--orange)"/>
      <g fill="#fff">
        <ellipse cx="44" cy="50" rx="26" ry="18"/>
        <rect x="12" y="43" width="10" height="12" rx="3"/>
        <rect x="26" y="60" width="9" height="14" rx="3"/>
        <rect x="52" y="60" width="9" height="14" rx="3"/>
        <circle cx="57" cy="24" r="10"/>
      </g>
      <circle cx="57" cy="24" r="10" fill="none" stroke="var(--orange)" stroke-width="2.5"/>
      <circle cx="30" cy="44" r="2.5" fill="var(--orange)"/>
    </svg>
    <div class="step__text" style="left:585px; top:41px;">
      <p class="step__head">BEST-TARIF<br>WECHSEL</p>
      <p class="step__body">Fordern Sie kostenlos und unverbind-<br>lich ein angebot für die senkung ihrer<br>strom- und /oder Gaskosten</p>
    </div>

    <p class="cycle-label">DAUERHAFT<br>SPAREN</p>

    <!-- Schritt 4 -->
    <span class="step__num" style="left:645px; top:220px;">4</span>
    <svg class="step__badge" style="left:675px; top:193px;" viewBox="0 0 90 90" role="img" aria-label="Symbol: Kreislaufpfeile">
      <circle cx="45" cy="45" r="45" fill="var(--orange)"/>
      <g fill="none" stroke="#fff" stroke-width="8">
        <path d="M20 40 a26 20 0 0 1 46 -6"/>
        <path d="M70 50 a26 20 0 0 1 -46 6"/>
      </g>
      <g fill="#fff">
        <polygon points="58,24 76,30 64,44"/>
        <polygon points="32,66 14,60 26,46"/>
      </g>
    </svg>
    <div class="step__text" style="left:600px; top:292px;">
      <p class="step__head">TARIF-CHECK<br>ANFORDERN</p>
      <p class="step__body">Fordern Sie kostenlos und unverbindlich<br>ein angebot für die senkung ihrer strom-<br>und /oder Gaskosten</p>
    </div>
  </section>

</body>
</html>
```